Communication and Marketing agency needs a new presentation card

We are a group of communication and marketing agencies specialized in companies that are in the logistics and industrial sector. The head agency is TELVANO Grupo and the group consists of 4 agencies: TELVANO Media, TELVANO Digital, TELVANO Research and DifundeEnPantalla. We hace 4 offices in Spain (Madrid, Barcelona, Valencia and Murcia). We are looking for a clean and attractive design that transmits our experience, brand presence in the market and knowledge to those who receive the card.It has to maintain the colors of the logo that is attached.
Target Market(s)
logistics and industrial sector
Marketing department
Contact Information for Business Card
Clean and attractive design

```html
<!DOCTYPE html>
<html lang="en">
<head>
<meta charset="utf-8">
<title>TELVANO Media – Business Card</title>
<link rel="stylesheet" href="https://fonts.googleapis.com/css2?family=Open+Sans:wght@400;600;700&display=swap">
<style>
  :root {
    --backdrop: #25262a;
    --card-dark: #231f20;
    --card-light: #ffffff;
    --brand-red: #b5121b;
    --icon-red: #e0161e;
    --ink-grey: #3a3a3a;
    --ink-white: #f2f2f2;
  }
  * { margin: 0; padding: 0; box-sizing: border-box; }
  html, body {
    width: 1200px; height: 960px; overflow: hidden;
    background: var(--backdrop);
    font-family: "Open Sans", Arial, sans-serif;
  }
  .canvas {
    position: relative; width: 1200px; height: 960px;
  }
  .card {
    position: absolute; left: 250px; width: 700px; height: 400px;
    box-shadow: 0 12px 30px rgba(0,0,0,0.45);
    overflow: hidden;
  }
  .card--front { top: 50px; background: var(--card-dark); }
  .card--back { top: 500px; background: var(--card-light); }

  .brand-name {
    font-weight: 600; color: var(--brand-red);
    letter-spacing: 1px; white-space: nowrap;
  }
  .card--front .brand-name {
    position: absolute; top: 150px; left: 0; width: 100%;
    text-align: center; font-size: 54px; line-height: 1.2;
  }
  .card--front .front-web {
    position: absolute; top: 290px; left: 0; width: 100%;
    text-align: center; font-size: 17px; color: var(--ink-white);
  }

  .card--back .brand-name {
    position: absolute; top: 48px; right: 48px; font-size: 34px; line-height: 1.2;
  }
  .holder {
    position: absolute; left: 56px; top: 130px;
  }
  .holder-name {
    font-size: 30px; font-weight: 700; color: var(--brand-red);
    text-transform: uppercase; letter-spacing: 0.5px; line-height: 1.1;
  }
  .holder-role {
    font-size: 20px; color: var(--ink-grey); margin-top: 2px; line-height: 1.3;
  }
  .address {
    margin-top: 16px; font-size: 20px; color: var(--brand-red); line-height: 1.25;
  }
  .contact-list { list-style: none; margin-top: 8px; }
  .contact-list li {
    display: flex; align-items: center; gap: 12px;
    font-size: 20px; color: var(--ink-grey); line-height: 1.4;
  }
  .contact-icon {
    width: 22px; height: 22px; flex: none;
  }
</style>
</head>
<body>
<main class="canvas">
  <section class="card card--front" aria-label="Card front">
    <div class="brand-name">TELVANO Media</div>
    <div class="front-web">www.telvanomedia.com</div>
  </section>

  <section class="card card--back" aria-label="Card back">
    <div class="brand-name">TELVANO Media</div>
    <div class="holder">
      <div class="holder-name">Marcela Ortiz</div>
      <div class="holder-role">CEO</div>
      <div class="address">418 Calle Almendro<br>Valencia, VC 46021</div>
      <ul class="contact-list">
        <li>
          <svg class="contact-icon" viewBox="0 0 22 22" aria-hidden="true">
            <circle cx="11" cy="11" r="11" fill="var(--icon-red)"/>
            <path d="M7.5 6 L9.3 6 L10 8.6 L8.9 9.5 Q10 12 12.5 13.1 L13.4 12 L16 12.7 L16 14.5 Q15.5 16 13.5 15.7 Q8 14.5 6.3 8.5 Q6 6.5 7.5 6 Z" fill="#fff"/>
          </svg>
          555.014.2290
        </li>
        <li>
          <svg class="contact-icon" viewBox="0 0 22 22" aria-hidden="true">
            <circle cx="11" cy="11" r="11" fill="var(--icon-red)"/>
            <rect x="5.5" y="7.5" width="11" height="7.5" rx="1" fill="#fff"/>
            <path d="M5.8 8 L11 12 L16.2 8" fill="none" stroke="var(--icon-red)" stroke-width="1.2"/>
          </svg>
          hola@telvanomedia.com
        </li>
        <li>
          <svg class="contact-icon" viewBox="0 0 22 22" aria-hidden="true">
            <circle cx="11" cy="11" r="11" fill="var(--icon-red)"/>
            <circle cx="11" cy="11" r="5.5" fill="none" stroke="#fff" stroke-width="1.3"/>
            <ellipse cx="11" cy="11" rx="2.3" ry="5.5" fill="none" stroke="#fff" stroke-width="1.1"/>
            <line x1="5.5" y1="11" x2="16.5" y2="11" stroke="#fff" stroke-width="1.1"/>
          </svg>
          www.telvanomedia.com
        </li>
      </ul>
    </div>
  </section>
</main>
</body>
</html>
```